Presentation Folder, for Cancer Awareness, VERY COLORFULL AND MODERN

This will be a standard size folder that will hold standard 8 1/2 x 11 papers with a business card slot on the flap, this is a very easy project with very little text and the design for the back page is already done so all you really have to do is make a very nice colorful front cover, you will see my attachments are labeled and I gave you alot of instructions, this should be a very fast easy project
Updates

Reason: there has not been enough quality designs, sorry

Target Market(s)

Our Target Market is Dr's that Deal with Cancer patients

Industry/Entity Type

Healthcare

Font styles to use
Serif

Colors

Designer to choose colors to be used in the design.

Requirements
Must have
• Project must be tasteful and look professional with the ribbons as the main focal point in the center of folder the folder should be a nice gray color to accent the color of the ribbons , the back page needs no design it is the" Sorvane Test" in the attachments I sent
Nice to have
• I would like the ribbons displayed in a row, I included a logo sample layout
• a picture on the front of the folder under the words Hereditary Cancer Screening - Then under that put the words - The Power of Knowledge - then add the picture I labeled Great Picture in the attachments

```html
<!DOCTYPE html>
<html lang="en">
<head>
<meta charset="utf-8">
<title>Sorvane Test – Hereditary Cancer Screening Folder</title>
<link rel="stylesheet" href="https://fonts.googleapis.com/css2?family=Roboto:wght@300;400;700&display=swap">
<style>
  :root {
    --backdrop: #d9d9db;
    --paper: #f3f3f3;
    --paper-shade: #e6e6e7;
    --magenta: #c8185e;
    --magenta-deep: #a81350;
    --magenta-light: #e0609a;
    --ink: #3a3a3a;
    --ink-soft: #8a8a8a;
  }
  * { box-sizing: border-box; margin: 0; padding: 0; }
  html, body {
    width: 1200px; height: 847px; overflow: hidden;
    background: var(--backdrop);
    font-family: "Roboto", Arial, sans-serif;
  }
  .folder {
    position: absolute; left: 110px; top: 70px;
    width: 980px; height: 700px;
    display: flex;
  }
  .panel {
    position: relative; width: 490px; height: 700px;
    background: var(--paper); overflow: hidden;
  }
  .panel--inside-left { background: linear-gradient(90deg, var(--paper) 80%, var(--paper-shade)); }
  .panel--inside-right { background: linear-gradient(90deg, var(--paper-shade), var(--paper) 20%); }
  .pocket {
    position: absolute; left: 0; right: 0; bottom: 0; height: 210px;
    background: var(--magenta);
  }
  .panel--inside-left .pocket { background: linear-gradient(90deg, var(--magenta) 70%, var(--magenta-deep)); }
  .panel--inside-right .pocket { background: linear-gradient(90deg, var(--magenta-deep), var(--magenta) 30%); }
  .card-slot { position: absolute; left: 60px; top: 6px; }

  .cancer-types {
    position: absolute; right: 58px; top: 72px;
    list-style: none; text-align: right;
    font-size: 13px; font-weight: 300; line-height: 19px;
    color: var(--ink-soft);
  }
  .cancer-word {
    position: absolute; right: 16px; top: 70px;
    writing-mode: vertical-rl; transform: rotate(180deg);
    font-size: 34px; font-weight: 300; letter-spacing: 5px;
    color: var(--magenta-light); line-height: 1;
  }
  .lab-intro {
    position: absolute; left: 40px; top: 362px; width: 300px;
    font-size: 10.5px; line-height: 15.5px; text-align: justify;
    color: var(--ink);
  }
  .lab-sponsor {
    position: absolute; left: 40px; top: 448px;
    font-size: 10.5px; line-height: 13px; color: var(--ink);
  }
  .lab-sponsor strong { font-weight: 700; display: block; }

  .ribbon-art {
    position: absolute; left: 135px; top: 70px;
    width: 200px; height: 290px;
    border-radius: 90px 90px 20px 20px;
    background: linear-gradient(160deg, var(--magenta-light), var(--magenta) 60%, var(--magenta-deep));
  }
</style>
</head>
<body>
  <main class="folder">
    <section class="panel panel--inside-left">
      <ul class="cancer-types">
        <li>Breast</li><li>Ovarian</li><li>Endometrial</li><li>Gastric</li><li>Colorectal</li>
        <li>Pancreatic</li><li>Melanoma</li><li>Prostate</li><li>Lung</li><li>Colon</li>
      </ul>
      <div class="cancer-word">CANCER</div>
      <p class="lab-intro">At our state of the art, CLIA certified and COLA accredited facility we perform Next Generation Sequencing (NGS) based screening for mutations known to affect an individual's Risk of developing Hereditary Cancer. Results from the test enable the Physician to make Better informed treatment decisions.</p>
      <p class="lab-sponsor"><strong>Halden Care Partners</strong>an independent arm of Veramont Labs LLC</p>
      <div class="pocket">
        <svg class="card-slot" width="340" height="70" viewBox="0 0 340 70" aria-hidden="true">
          <path d="M10 58 Q120 20 330 28" fill="none" stroke="var(--magenta-deep)" stroke-width="1.5"/>
          <circle cx="160" cy="34" r="16" fill="none" stroke="var(--magenta-deep)" stroke-width="1.5"/>
          <path d="M110 20 Q140 6 175 14" fill="none" stroke="var(--magenta-light)" stroke-width="1"/>
        </svg>
      </div>
    </section>
    <section class="panel panel--inside-right">
      <div class="ribbon-art" role="img" aria-label="Magenta awareness ribbon with a leaping figure silhouette"></div>
      <div class="pocket"></div>
    </section>
  </main>
</body>
</html>
```